Breakfast Cafe - The Sunny Nook

It is for my breakfast and lunch cafe with a hawaiian / beach theme. I am open 7 days a week from 7am to 2pm. We serve traditional American food such as omelettes, pancakes, burgers and sandwiches. I'll upload my old card and my new logo to be used. We have a lot of day to day regulars who eat there during the week, our t-shirts actually say 'Locals Only' on them. Hope this helps. Thanks.

Target Market(s)

anyone who has an appetite!

Industry/Entity Type

American Restaurant

Contact Information for Business Card

4815C Marlow Grove Avenue
Long Beach, California
(555) 731-2294

Requirements
Must have
• Address and phone number easily readable.
Nice to have
• beach or tropical theme

```html
<!DOCTYPE html>
<html lang="en">
<head>
<meta charset="utf-8">
<title>The Sunny Nook – Business Card</title>
<link href="https://fonts.googleapis.com/css2?family=Roboto:ital,wght@0,400;0,500;0,700;1,500&display=swap" rel="stylesheet">
<style>
  :root {
    --backdrop: #d6d6d6;
    --card-light: #f4f4f4;
    --brand-brown: #b06112;
    --ink-dark: #3a3a3a;
    --ink-mid: #444444;
    --white: #ffffff;
    --bullet: #d9d9d9;
  }
  html, body {
    margin: 0;
    padding: 0;
    width: 1200px;
    height: 900px;
    overflow: hidden;
    background: var(--backdrop);
    font-family: "Roboto", Arial, sans-serif;
  }
  .canvas {
    position: relative;
    width: 1200px;
    height: 900px;
  }
  .card {
    position: absolute;
    top: 200px;
    width: 310px;
    height: 500px;
    box-sizing: border-box;
  }
  .card--front {
    left: 308px;
    background: var(--card-light);
    border-radius: 62px 0 62px 0;
  }
  .card--back {
    left: 641px;
    background: var(--brand-brown);
    border-radius: 0 62px 0 62px;
    color: var(--white);
  }
  .brand-mark {
    position: absolute;
    left: 0;
    right: 0;
    top: 38px;
    text-align: center;
  }
  .brand-mark__circle {
    display: block;
    width: 150px;
    height: 150px;
    margin: 0 auto;
    border-radius: 50%;
    background: radial-gradient(circle at 50% 40%, #f6b64a, #e08a2a 70%, #9a5a1e);
  }
  .brand-mark__name {
    margin-top: 8px;
    font-size: 30px;
    font-weight: 700;
    color: var(--brand-brown);
    line-height: 1;
  }
  .brand-mark__place {
    margin-top: 6px;
    font-size: 10px;
    font-weight: 700;
    letter-spacing: 2.5px;
    color: var(--brand-brown);
  }
  .contact {
    position: absolute;
    left: 26px;
    top: 312px;
    right: 20px;
  }
  .contact__phone {
    display: flex;
    align-items: center;
    gap: 7px;
    font-size: 19px;
    color: var(--brand-brown);
  }
  .contact__icon {
    width: 27px;
    height: 27px;
    background: var(--brand-brown);
    border-radius: 3px;
    display: flex;
    align-items: center;
    justify-content: center;
  }
  .contact__name {
    margin-top: 14px;
    font-size: 21px;
    font-weight: 500;
    color: var(--ink-dark);
  }
  .contact__address {
    margin-top: 5px;
    font-size: 14px;
    line-height: 19px;
    color: var(--ink-mid);
  }
  .contact__tagline {
    margin-top: 16px;
    font-size: 17px;
    font-style: italic;
    font-weight: 500;
    color: var(--ink-dark);
  }
  .back-brand {
    position: absolute;
    left: 0;
    right: 0;
    top: 80px;
    text-align: center;
  }
  .back-brand__name {
    font-size: 34px;
    font-weight: 700;
    line-height: 1;
  }
  .back-brand__place {
    margin-top: 8px;
    font-size: 11px;
    font-weight: 700;
    letter-spacing: 2.8px;
  }
  .menu {
    position: absolute;
    left: 48px;
    top: 295px;
    margin: 0;
    padding: 0;
    list-style: none;
    font-size: 18px;
    line-height: 23px;
  }
  .menu li::before {
    content: "";
    display: inline-block;
    width: 7px;
    height: 7px;
    border-radius: 50%;
    background: var(--bullet);
    margin: 0 8px 3px -15px;
  }
  .hours {
    position: absolute;
    left: 48px;
    top: 402px;
    font-size: 21px;
    line-height: 28px;
    font-style: italic;
    font-weight: 500;
  }
</style>
</head>
<body>
<main class="canvas">
  <section class="card card--front">
    <div class="brand-mark">
      <span class="brand-mark__circle" role="img" aria-label="Round beach-themed badge area in sunset orange tones"></span>
      <div class="brand-mark__name">The Sunny Nook</div>
      <div class="brand-mark__place">LONG BEACH, CA</div>
    </div>
    <div class="contact">
      <div class="contact__phone">
        <span class="contact__icon">
          <svg width="17" height="17" viewBox="0 0 24 24" aria-hidden="true">
            <path fill="#ffffff" d="M6.6 10.8c1.4 2.8 3.8 5.1 6.6 6.6l2.2-2.2c.3-.3.7-.4 1-.2 1.1.4 2.3.6 3.6.6.6 0 1 .4 1 1V20c0 .6-.4 1-1 1C10.6 21 3 13.4 3 4c0-.6.4-1 1-1h3.5c.6 0 1 .4 1 1 0 1.3.2 2.5.6 3.6.1.3 0 .7-.2 1L6.6 10.8z"/>
          </svg>
        </span>
        (555) 731-2294
      </div>
      <div class="contact__name">THE SUNNY NOOK</div>
      <div class="contact__address">4815C Marlow Grove Avenue<br>Long Beach, California</div>
      <div class="contact__tagline">Family owned and operated!</div>
    </div>
  </section>

  <section class="card card--back">
    <div class="back-brand">
      <div class="back-brand__name">The Sunny Nook</div>
      <div class="back-brand__place">LONG BEACH, CA</div>
    </div>
    <ul class="menu">
      <li>Omelettes</li>
      <li>Pancakes</li>
      <li>Burgers</li>
      <li>Sandwiches</li>
    </ul>
    <div class="hours">Breakfast &amp; Lunch<br>7am - 2pm Daily</div>
  </section>
</main>
</body>
</html>
```